Global (re)insurance broker needs a business card design

We need a classic business card for our company that is headquartered in SG, with offices in Malaysia and Dubai. We specialise in insurance and reinsurance broking and consultancy for our global clients.

```html
<!DOCTYPE html>
<html lang="en">
<head>
<meta charset="utf-8">
<title>Meridane – Business Card</title>
<link rel="stylesheet" href="https://fonts.googleapis.com/css2?family=Open+Sans:wght@400;600;700&display=swap">
<style>
  :root {
    --brand-blue: #24479b;
    --brand-blue-light: #3157b8;
    --brand-green: #b9d8ad;
    --card-white: #f4f4f4;
    --ink: #1d1d1d;
    --page: #e6e7ea;
  }
  * { margin: 0; padding: 0; box-sizing: border-box; }
  html, body {
    width: 1200px; height: 780px; overflow: hidden;
    background: var(--page);
    font-family: "Open Sans", Arial, sans-serif;
  }
  .sheet {
    width: 1200px; height: 780px;
    display: flex; align-items: center; justify-content: center; gap: 40px;
  }
  .card {
    position: relative; width: 540px; height: 308px; overflow: hidden;
    box-shadow: 0 6px 18px rgba(0,0,0,.18);
  }
  /* Front */
  .card--front { background: var(--card-white); }
  .front__swoosh { position: absolute; inset: 0; width: 100%; height: 100%; }
  .front__brand {
    position: absolute; left: 200px; top: 40px;
    font-weight: 700; font-size: 50px; letter-spacing: 1px;
    color: var(--brand-blue);
  }
  .front__person { position: absolute; left: 34px; top: 118px; }
  .person__name { font-weight: 700; font-size: 27px; line-height: 1.1; color: var(--brand-blue); }
  .person__name .surname { color: var(--brand-green); }
  .person__title { font-size: 13px; color: var(--ink); margin-top: 2px; }
  .front__divider {
    position: absolute; left: 222px; top: 118px; width: 2px; height: 64px;
    background: var(--ink);
  }
  .front__contacts {
    position: absolute; left: 238px; top: 120px; list-style: none;
    font-size: 13px; color: var(--ink); line-height: 21px;
  }
  .front__contacts li { display: flex; align-items: center; gap: 8px; }
  .contact__icon { width: 12px; height: 12px; flex: none; }
  .front__address {
    position: absolute; left: 24px; bottom: 12px;
    font-size: 12px; color: #ffffff; letter-spacing: .2px; white-space: nowrap;
  }
  /* Back */
  .card--back {
    background: linear-gradient(120deg, var(--brand-blue) 0%, var(--brand-blue-light) 60%, #4a6ec8 100%);
    display: flex; align-items: center; justify-content: center;
  }
  .back__texture { position: absolute; inset: 0; background: linear-gradient(120deg, rgba(0,0,0,.06), rgba(255,255,255,.08)); }
  .back__brand {
    position: relative; font-weight: 700; font-size: 56px; letter-spacing: 1px;
    color: #ffffff;
  }
</style>
</head>
<body>
<main class="sheet">
  <section class="card card--front" aria-label="Card front">
    <svg class="front__swoosh" viewBox="0 0 540 308" aria-hidden="true">
      <path d="M0,190 C80,268 250,272 540,266 L540,308 L0,308 Z" fill="var(--brand-blue)"/>
      <path d="M20,190 C100,254 270,258 522,254" fill="none" stroke="var(--brand-green)" stroke-width="3"/>
    </svg>
    <div class="front__brand">MERIDANE</div>
    <div class="front__person">
      <div class="person__name">Lena <span class="surname">Koh</span></div>
      <div class="person__title">Chief Operating Officer</div>
    </div>
    <div class="front__divider"></div>
    <ul class="front__contacts">
      <li>
        <svg class="contact__icon" viewBox="0 0 12 12" aria-hidden="true"><rect x="2.5" y="0.5" width="7" height="11" rx="1.2" fill="none" stroke="var(--brand-green)"/></svg>
        +65 6100 2468
      </li>
      <li>
        <svg class="contact__icon" viewBox="0 0 12 12" aria-hidden="true"><circle cx="6" cy="6" r="5.5" fill="var(--brand-blue)"/><path d="M0.5,6 H11.5 M6,0.5 V11.5" stroke="#fff" stroke-width=".8"/></svg>
        www.meridane.com
      </li>
      <li>
        <svg class="contact__icon" viewBox="0 0 12 12" aria-hidden="true"><rect x="0.5" y="2.5" width="11" height="7" fill="none" stroke="var(--brand-green)"/><path d="M0.5,2.5 L6,7 L11.5,2.5" fill="none" stroke="var(--brand-green)"/></svg>
        lena@meridane.com
      </li>
    </ul>
    <div class="front__address">88 Harbour Street, Quayside Tower #12-04, Singapore 068912</div>
  </section>

  <section class="card card--back" aria-label="Card back">
    <div class="back__texture" role="img" aria-label="Faint repeating company-name pattern across the blue background"></div>
    <div class="back__brand">MERIDANE</div>
  </section>
</main>
</body>
</html>
```